Larkfield Ridge Management

I need a professional website. My current website is larkfieldridgemanagement.com and I hate it. It was created with some AI tool very quickly because I needed a site up and running with no advanced notice. I’m open to all designs .. I trust you, the professionals will deliver the results I’m anxiously awaiting! :)

```html
<!DOCTYPE html>
<html lang="en">
<head>
<meta charset="utf-8">
<title>Larkfield Ridge Management</title>
<link rel="stylesheet" href="https://fonts.googleapis.com/css2?family=Poppins:ital,wght@0,400;0,500;0,600;0,700;1,400&display=swap">
<style>
:root{
  --navy:#233559;
  --navy-deep:#1c2a47;
  --red:#8c1b2c;
  --ink:#1e2434;
  --muted:#5f6473;
  --line:#dfe2e8;
  --soft:#f2f3f6;
  --footer:#1b2131;
  --white:#ffffff;
  --gold:#f2b01e;
}
*{box-sizing:border-box;margin:0;padding:0}
html,body{width:1200px;height:3974px;overflow:hidden}
body{font-family:'Poppins',sans-serif;color:var(--ink);background:var(--white);position:relative}
a{color:inherit;text-decoration:none}
.section{position:absolute;left:0;width:1200px}
.btn{display:inline-flex;align-items:center;justify-content:center;background:var(--red);color:var(--white);font-size:11px;font-weight:600;text-transform:uppercase;letter-spacing:.2px}
.section-title{text-align:center;font-size:37px;font-weight:400;color:var(--ink);letter-spacing:.3px;text-transform:uppercase}
.section-title b{font-weight:600;color:var(--navy)}

/* header */
.header{top:0;height:124px;background:var(--white)}
.topbar{position:absolute;left:300px;top:0;width:900px;height:37px;background:var(--navy);clip-path:polygon(0 0,100% 0,100% 100%,28px 100%);color:var(--white);font-size:12px}
.topbar .social{position:absolute;left:50px;top:10px;display:flex;gap:22px}
.topbar .social span{width:15px;height:15px;border:1.5px solid rgba(255,255,255,.85);border-radius:3px;display:block}
.topbar .contact{position:absolute;right:60px;top:10px;display:flex;gap:36px}
.topbar .contact span{display:flex;align-items:center;gap:8px}
.brand{position:absolute;left:58px;top:22px;display:flex;align-items:center;gap:10px;width:220px}
.brand-mark{width:26px;height:26px;background:var(--navy);flex:none}
.brand-name{font-size:15px;font-weight:600;color:var(--navy);line-height:1.25}
.nav{position:absolute;left:329px;top:72px;display:flex;font-size:13px;color:var(--ink)}
.nav a{margin-right:0}
.nav .active{color:var(--red);font-weight:500}
.header .cta{position:absolute;left:979px;top:62px;width:161px;height:40px}

/* hero */
.hero{top:124px;height:655px;overflow:hidden}
.hero-photo{position:absolute;inset:0;background:linear-gradient(100deg,#2b3a5c 0%,#34476b 35%,#6a6f7a 60%,#8a7f78 78%,#4b5670 100%)}
.hero-shade{position:absolute;inset:0;background:linear-gradient(90deg,rgba(30,44,78,.75) 0%,rgba(30,44,78,.35) 55%,rgba(30,44,78,0) 100%)}
.hero-copy{position:absolute;left:160px;top:195px;color:var(--white)}
.hero-copy h1{font-size:40px;line-height:48px;font-weight:600;text-transform:uppercase;letter-spacing:.3px}
.hero-copy p{font-size:13px;margin-top:4px}
.hero-copy .btn{margin-top:28px;width:138px;height:34px}
.hero-arrow{position:absolute;top:275px;width:14px;height:24px}
.hero-shape{position:absolute;left:0;top:0}

/* services */
.services{top:779px;height:632px}
.services .section-title{margin-top:40px}
.service-cards{position:absolute;left:160px;top:128px;display:flex;gap:24px}
.service-card{width:277px;height:345px;border:1px solid var(--line);border-radius:4px;background:var(--white);position:relative;text-align:center}
.service-card.raised{box-shadow:0 10px 28px rgba(20,30,60,.12)}
.service-photo{height:180px;border-radius:4px 4px 0 0}
.service-icon{position:absolute;left:108px;top:150px;width:60px;height:60px;border-radius:50%;border:4px solid var(--white);display:flex;align-items:center;justify-content:center}
.service-card h3{margin-top:46px;font-size:16px;font-weight:600;line-height:20px;padding:0 30px}
.service-card p{font-size:11px;color:var(--muted);line-height:14px;margin:14px 36px 0}
.service-card .more{display:inline-block;margin-top:14px;font-size:11px;font-weight:600;color:var(--navy)}
.service-card.raised .more{color:var(--red);border-bottom:3px solid var(--red);padding:0 20px 6px}
.services .btn{position:absolute;left:515px;top:520px;width:170px;height:37px}

/* about */
.about{top:1411px;height:437px}
.about-panel{position:absolute;left:0;top:0;width:600px;height:437px;background:var(--navy);color:var(--white)}
.about-panel h2{position:absolute;left:162px;top:56px;font-size:37px;font-weight:500;letter-spacing:.3px}
.about-panel .copy{position:absolute;left:162px;top:120px;width:360px;font-size:13px;line-height:19.5px}
.about-panel .copy p+p{margin-top:20px}
.about-panel .btn{position:absolute;left:162px;top:338px;width:138px;height:34px}
.about-photo{position:absolute;left:600px;top:0;width:600px;height:437px;background:linear-gradient(135deg,#dfe2e6 0%,#c9cdd3 40%,#8e9aa8 70%,#2b3652 100%)}

/* how it works */
.how{top:1848px;height:558px}
.how .section-title{margin-top:66px}
.step{position:absolute;width:280px;font-size:13px;color:var(--muted);line-height:20px}
.step h4{font-size:16px;font-weight:600;color:var(--ink);margin-bottom:4px}
.step.center{left:460px;top:146px;text-align:center}
.step.left{left:162px;top:265px}
.step.right{left:758px;top:265px;text-align:right}
.step-icon{height:62px;display:flex;align-items:flex-end}
.step.center .step-icon{justify-content:center}
.step.right .step-icon{justify-content:flex-end}
.how-brand{position:absolute;left:450px;top:340px;width:300px;text-align:center}
.how-brand .brand-mark{width:46px;height:46px;margin:0 auto 12px}
.how-brand span{font-size:26px;font-weight:600;color:var(--navy);line-height:32px;display:block}
.how-arrow{position:absolute}

/* testimonials */
.testimonials{top:2406px;height:506px;background:var(--soft)}
.testimonials .section-title{margin-top:66px}
.testimonial{position:absolute;top:178px;width:405px}
.rating{display:flex;align-items:center;gap:4px;font-size:13px;font-weight:500}
.stars{color:var(--gold);font-size:15px;letter-spacing:1px}
.testimonial blockquote{margin-top:10px;font-size:13px;font-style:italic;color:var(--muted);line-height:19.5px}
.author{margin-top:16px;display:flex;align-items:center;gap:18px;position:relative}
.avatar{width:54px;height:54px;border-radius:50%;background:linear-gradient(160deg,#c7c2bd,#7c7470)}
.author .name{font-size:14px;color:var(--muted);line-height:18px}
.author .org{font-size:14px;font-weight:500;color:var(--ink)}
.quote-mark{position:absolute;right:0;top:-10px;font-size:80px;font-weight:700;color:#8a8e99;line-height:1;font-family:Georgia,serif}
.t-arrow{position:absolute;top:264px;width:10px;height:18px}
.testimonials .btn{position:absolute;left:515px;top:421px;width:170px;height:37px}

/* news */
.news{top:2912px;height:620px}
.news .section-title{margin-top:54px}
.news-cards{position:absolute;left:160px;top:139px;display:flex;gap:24px}
.news-card{width:277px}
.news-photo{height:216px}
.news-meta{margin-top:18px;display:flex;align-items:center;gap:30px;font-size:12px;color:var(--muted)}
.news-meta span{display:flex;align-items:center;gap:8px}
.news-card h3{margin-top:14px;font-size:15px;font-weight:500;line-height:19px}
.news-card p{margin-top:10px;font-size:11px;line-height:14px;color:var(--muted)}
.news-card .more{display:inline-block;margin-top:14px;font-size:11px;font-weight:600;color:var(--red);letter-spacing:1.5px}
.news .btn{position:absolute;left:515px;top:571px;width:170px;height:37px}

/* footer */
.footer{top:3532px;height:442px;background:var(--footer);color:var(--white)}
.footer-shape{position:absolute;left:0;top:0}
.footer-brand{position:absolute;left:190px;top:212px;width:140px;text-align:center}
.footer-brand .brand-mark{background:var(--white);margin:0 auto 10px;width:34px;height:34px}
.footer-brand .brand-name{color:var(--white);font-size:15px}
.footer-social{position:absolute;left:198px;top:338px;display:flex;gap:26px}
.footer-social span{width:15px;height:15px;border:1.5px solid var(--white);border-radius:3px;display:block}
.footer-col{position:absolute;top:200px}
.footer-col h5{font-size:16px;font-weight:500;padding-bottom:10px;position:relative}
.footer-col h5:after{content:"";position:absolute;left:0;bottom:0;width:46px;height:2px;background:var(--red)}
.footer-col ul{list-style:none;margin-top:18px;font-size:13px}
.footer-col li{height:37px}
.footer-col.contact li{display:flex;align-items:center;gap:14px;height:38px}
.dot{width:26px;height:26px;border-radius:50%;background:var(--red);display:flex;align-items:center;justify-content:center;flex:none}
</style>
</head>
<body>

<header class="section header">
  <div class="topbar">
    <div class="social"><span></span><span></span><span></span></div>
    <div class="contact">
      <span><svg width="12" height="12" viewBox="0 0 24 24" fill="#fff"><path d="M6.6 10.8a15.1 15.1 0 0 0 6.6 6.6l2.2-2.2a1 1 0 0 1 1-.25 11.4 11.4 0 0 0 3.6.6 1 1 0 0 1 1 1V20a1 1 0 0 1-1 1A17 17 0 0 1 3 4a1 1 0 0 1 1-1h3.5a1 1 0 0 1 1 1c0 1.25.2 2.45.6 3.6a1 1 0 0 1-.25 1z"/></svg>727-555-0148</span>
      <span><svg width="13" height="10" viewBox="0 0 24 18" fill="#fff"><path d="M0 0h24v18H0z" opacity=".9"/><path d="M0 0l12 9 12-9" stroke="#233559" stroke-width="2" fill="none"/></svg>info@larkfieldridgemanagement.com</span>
    </div>
  </div>
  <div class="brand"><div class="brand-mark"></div><div class="brand-name">Larkfield Ridge<br>Management</div></div>
  <nav class="nav">
    <a class="active" href="#" style="width:87px">Home</a>
    <a href="#" style="width:122px">About Us</a>
    <a href="#" style="width:110px">Services</a>
    <a href="#" style="width:140px">How It Works</a>
    <a href="#" style="width:86px">News</a>
    <a href="#">Contact Us</a>
  </nav>
  <a class="btn cta" href="#">Book Consultation</a>
</header>

<section class="section hero">
  <div class="hero-photo" role="img" aria-label="Modern two-storey house with wood cladding and large glass windows at dusk"></div>
  <div class="hero-shade"></div>
  <div class="hero-copy">
    <h1>Professional Property<br>Management You<br>Can Trust</h1>
    <p>A true partner, not just a vendor.</p>
    <a class="btn" href="#">Learn More</a>
  </div>
  <svg class="hero-arrow" style="left:30px" viewBox="0 0 14 24"><path d="M12 2L2 12l10 10" stroke="#fff" stroke-width="2" fill="none"/></svg>
  <svg class="hero-arrow" style="left:1156px" viewBox="0 0 14 24"><path d="M2 2l10 10L2 22" stroke="#fff" stroke-width="2" fill="none"/></svg>
  <svg class="hero-shape" width="1200" height="655" viewBox="0 0 1200 655">
    <polygon points="0,628 856,532 1200,640 1200,655 0,655" fill="#8c1b2c"/>
    <polygon points="0,655 856,562 1200,660 1200,655" fill="#fff"/>
  </svg>
</section>

<section class="section services">
  <h2 class="section-title">Our <b>Services</b></h2>
  <div class="service-cards">
    <article class="service-card">
      <div class="service-photo" role="img" aria-label="White family house with blue roof at sunset" style="background:linear-gradient(160deg,#a9b6c8,#6f7c66 60%,#b48a55)"></div>
      <div class="service-icon" style="background:var(--navy)"><svg width="24" height="22" viewBox="0 0 24 22" fill="#fff"><path d="M12 1L1 11h3v10h6v-6h4v6h6V11h3z"/></svg></div>
      <h3>Residential Property Management</h3>
      <p>It is a long established fact that a looking at its layout.</p>
      <a class="more" href="#">LEARN MORE</a>
    </article>
    <article class="service-card raised">
      <div class="service-photo" role="img" aria-label="Modern apartment towers with glass and brick facades" style="background:linear-gradient(160deg,#7fb2dc,#244b6b 55%,#b4673e)"></div>
      <div class="service-icon" style="background:var(--red)"><svg width="22" height="24" viewBox="0 0 22 24" fill="#fff"><path d="M3 2h16v22h-6v-5H9v5H3z"/><g fill="#8c1b2c"><rect x="6" y="5" width="3" height="3"/><rect x="13" y="5" width="3" height="3"/><rect x="6" y="11" width="3" height="3"/><rect x="13" y="11" width="3" height="3"/></g></svg></div>
      <h3>Commercial Property Management</h3>
      <p>It is a long established fact that a looking at its layout.</p>
      <a class="more" href="#">LEARN MORE</a>
    </article>
    <article class="service-card">
      <div class="service-photo" role="img" aria-label="Tenants reviewing documents with a property manager" style="background:linear-gradient(160deg,#d8d2c8,#9c8f80 55%,#5a6f8c)"></div>
      <div class="service-icon" style="background:var(--navy)"><svg width="26" height="20" viewBox="0 0 26 20" fill="none" stroke="#fff" stroke-width="2"><path d="M2 8l6-5 5 3 5-3 6 5-6 7-5-4-4 4z"/></svg></div>
      <h3>Tenant Placement</h3>
      <p>It is a long established fact that a reader will be distracted by th looking at its layout.</p>
      <a class="more" href="#">LEARN MORE</a>
    </article>
  </div>
  <a class="btn" href="#">View More Services</a>
</section>

<section class="section about">
  <div class="about-panel">
    <h2>ABOUT US</h2>
    <div class="copy">
      <p>Our organization delivers comprehensive property management solutions that optimize asset performance and tenant satisfaction.</p>
      <p>Drawing on decades of collective expertise, the team facilitates regulatory compliance, cost efficiency, and proactive maintenance. This disciplined approach enables owners to preserve capital, enhance occupancy rates, and demonstrate long-term resilience across diverse market conditions.</p>
    </div>
    <a class="btn" href="#">Learn More</a>
  </div>
  <div class="about-photo" role="img" aria-label="Two business people shaking hands over a model of buildings and trees"></div>
</section>

<section class="section how">
  <h2 class="section-title">How It <b>Works</b></h2>
  <div class="step center">
    <div class="step-icon"><svg width="52" height="58" viewBox="0 0 52 58" fill="none" stroke="#8c1b2c" stroke-width="3"><rect x="14" y="4" width="24" height="34" fill="#8c1b2c"/><path d="M3 44l14 8h18l14-10"/><g fill="#fff" stroke="none"><rect x="19" y="10" width="4" height="4"/><rect x="29" y="10" width="4" height="4"/><rect x="19" y="19" width="4" height="4"/><rect x="29" y="19" width="4" height="4"/></g></svg></div>
    <h4 style="margin-top:14px">Property Assessment</h4>
    <p>Lorem Ipsum is simply dummy text of the printing and typesetting industry.</p>
  </div>
  <div class="step left">
    <div class="step-icon" style="height:50px"><svg width="52" height="50" viewBox="0 0 24 24" fill="#233559"><path d="M6.6 10.8a15.1 15.1 0 0 0 6.6 6.6l2.2-2.2a1 1 0 0 1 1-.25 11.4 11.4 0 0 0 3.6.6 1 1 0 0 1 1 1V20a1 1 0 0 1-1 1A17 17 0 0 1 3 4a1 1 0 0 1 1-1h3.5a1 1 0 0 1 1 1c0 1.25.2 2.45.6 3.6a1 1 0 0 1-.25 1z"/></svg></div>
    <h4 style="margin-top:14px">Schedule a Consultation</h4>
    <p>Lorem Ipsum is simply dummy text of the printing and typesetting industry.</p>
  </div>
  <div class="step right">
    <div class="step-icon" style="height:58px"><svg width="56" height="56" viewBox="0 0 56 56" fill="#233559"><rect x="6" y="40" width="6" height="12"/><rect x="16" y="32" width="6" height="20"/><rect x="26" y="24" width="6" height="28"/><rect x="36" y="16" width="6" height="36"/><path d="M46 4l8 10h-5v36h-6V14h-5z"/></svg></div>
    <h4 style="margin-top:8px">Reports &amp; Support</h4>
    <p>Lorem Ipsum is simply dummy text of the printing and typesetting industry.</p>
  </div>
  <svg class="how-arrow" style="left:360px;top:250px" width="62" height="36" viewBox="0 0 62 36" fill="none" stroke="#7f8a9e" stroke-width="1.5"><path d="M2 34C14 14 34 6 58 6"/><path d="M50 1l8 5-7 5"/></svg>
  <svg class="how-arrow" style="left:770px;top:254px" width="56" height="36" viewBox="0 0 56 36" fill="none" stroke="#7f8a9e" stroke-width="1.5"><path d="M2 2c20 0 36 10 50 30"/><path d="M53 22l-1 10-8-4"/></svg>
  <div class="how-brand"><div class="brand-mark"></div><span>Larkfield Ridge<br>Management</span></div>
</section>

<section class="section testimonials">
  <h2 class="section-title">Client <b>Testimonial</b></h2>
  <svg class="t-arrow" style="left:30px" viewBox="0 0 10 18"><path d="M9 1L1 9l8 8" stroke="#8a8e99" stroke-width="1.5" fill="none"/></svg>
  <svg class="t-arrow" style="left:1160px" viewBox="0 0 10 18"><path d="M1 1l8 8-8 8" stroke="#8a8e99" stroke-width="1.5" fill="none"/></svg>
  <article class="testimonial" style="left:162px">
    <div class="rating"><span class="stars">★★★★★</span> 5.0</div>
    <blockquote>There are many variations of passages of Lorem Ipsum available, but the majority have suffered alteration in some form, by injected humour, you need to be sure there isn't anything embarrassing hidden in the middle of text. All the tend to repeat predefined chunks as necess.</blockquote>
    <div class="author"><div class="avatar" role="img" aria-label="Client portrait"></div><div><div class="name">Maya Ellison</div><div class="org">Harlow Trading Ltd.</div></div><span class="quote-mark">“</span></div>
  </article>
  <article class="testimonial" style="left:635px">
    <div class="rating"><span class="stars">★★★★★</span> 5.0</div>
    <blockquote>There are many variations of passages of Lorem Ipsum available, but the majority have suffered alteration in some form, by injected humour, you need to be sure there isn't anything embarrassing hidden in the middle of text. All the tend to repeat predefined chunks as necess.</blockquote>
    <div class="author"><div class="avatar" role="img" aria-label="Client portrait"></div><div><div class="name">Maya Ellison</div><div class="org">Harlow Trading Ltd.</div></div><span class="quote-mark">“</span></div>
  </article>
  <a class="btn" href="#">View All Testimonial</a>
</section>

<section class="section news">
  <h2 class="section-title">Latest <b>News</b></h2>
  <div class="news-cards">
    <article class="news-card">
      <div class="news-photo" role="img" aria-label="Residential apartment building with balconies and trees" style="background:linear-gradient(170deg,#8fbbe0,#c9c6bd 50%,#4d6b3e)"></div>
      <div class="news-meta"><span><svg width="16" height="16" viewBox="0 0 16 16"><rect x="1" y="2" width="14" height="13" fill="#233559"/><rect x="3" y="6" width="10" height="7" fill="#fff"/></svg>Feb 10,2026</span><span><svg width="18" height="14" viewBox="0 0 18 14" fill="none" stroke="#233559" stroke-width="1.5"><rect x="1" y="1" width="16" height="9" rx="3"/><path d="M4 10v3l3-3"/></svg>10 Comments</span></div>
      <h3>When To Seek Business For Your Advisory Support</h3>
      <p>It is a long established fact that a reader will be distracted by the looking at its layout.</p>
      <a class="more" href="#">LEARN MORE →</a>
    </article>
    <article class="news-card">
      <div class="news-photo" role="img" aria-label="Small house model on a tablet in warm sunlight" style="background:linear-gradient(160deg,#e7b04c,#a5642d 55%,#3d2c1f)"></div>
      <div class="news-meta"><span><svg width="16" height="16" viewBox="0 0 16 16"><rect x="1" y="2" width="14" height="13" fill="#233559"/><rect x="3" y="6" width="10" height="7" fill="#fff"/></svg>Feb 10,2026</span><span><svg width="18" height="14" viewBox="0 0 18 14" fill="none" stroke="#233559" stroke-width="1.5"><rect x="1" y="1" width="16" height="9" rx="3"/><path d="M4 10v3l3-3"/></svg>10 Comments</span></div>
      <h3>When To Seek Business For Your Advisory Support</h3>
      <p>It is a long established fact that a reader will be distracted by the looking at its layout.</p>
      <a class="more" href="#">LEARN MORE →</a>
    </article>
    <article class="news-card">
      <div class="news-photo" role="img" aria-label="Two business professionals talking outdoors" style="background:linear-gradient(160deg,#3f5a3b,#2c3340 50%,#c8c4bd)"></div>
      <div class="news-meta"><span><svg width="16" height="16" viewBox="0 0 16 16"><rect x="1" y="2" width="14" height="13" fill="#233559"/><rect x="3" y="6" width="10" height="7" fill="#fff"/></svg>Feb 10,2026</span><span><svg width="18" height="14" viewBox="0 0 18 14" fill="none" stroke="#233559" stroke-width="1.5"><rect x="1" y="1" width="16" height="9" rx="3"/><path d="M4 10v3l3-3"/></svg>10 Comments</span></div>
      <h3>When To Seek Business For Your Advisory Support</h3>
      <p>It is a long established fact that a reader will be distracted by the looking at its layout.</p>
      <a class="more" href="#">LEARN MORE →</a>
    </article>
  </div>
  <a class="btn" href="#">View All News</a>
</section>

<footer class="section footer">
  <svg class="footer-shape" width="1200" height="150" viewBox="0 0 1200 150">
    <polygon points="0,0 1200,0 1200,22 856,128 0,22" fill="#8c1b2c"/>
    <polygon points="0,0 1200,0 856,104 0,0" fill="#fff"/>
  </svg>
  <div class="footer-brand"><div class="brand-mark"></div><div class="brand-name">Larkfield Ridge<br>Management</div></div>
  <div class="footer-social"><span></span><span></span><span></span></div>
  <div class="footer-col" style="left:421px">
    <h5>Quick Links</h5>
    <ul><li>Home</li><li>About Us</li><li>Services</li><li>Contact Us</li></ul>
  </div>
  <div class="footer-col" style="left:589px">
    <h5>Services</h5>
    <ul><li>Residential Property</li><li>Commercial Property</li><li>Tenant Placement</li><li>Maintenance Coordination</li></ul>
  </div>
  <div class="footer-col contact" style="left:817px">
    <h5>Contact Us</h5>
    <ul>
      <li><span class="dot"><svg width="12" height="12" viewBox="0 0 24 24" fill="#fff"><path d="M6.6 10.8a15.1 15.1 0 0 0 6.6 6.6l2.2-2.2a1 1 0 0 1 1-.25 11.4 11.4 0 0 0 3.6.6 1 1 0 0 1 1 1V20a1 1 0 0 1-1 1A17 17 0 0 1 3 4a1 1 0 0 1 1-1h3.5a1 1 0 0 1 1 1c0 1.25.2 2.45.6 3.6a1 1 0 0 1-.25 1z"/></svg></span>727-555-0148</li>
      <li><span class="dot"><svg width="12" height="9" viewBox="0 0 24 18"><rect width="24" height="18" fill="#fff"/><path d="M0 0l12 9 12-9" stroke="#8c1b2c" stroke-width="2" fill="none"/></svg></span>info@larkfieldridgemanagement.com</li>
      <li><span class="dot"><svg width="10" height="13" viewBox="0 0 20 26" fill="#fff"><path d="M10 0a10 10 0 0 0-10 10c0 7 10 16 10 16s10-9 10-16A10 10 0 0 0 10 0zm0 14a4 4 0 1 1 0-8 4 4 0 0 1 0 8z"/></svg></span>122, Lorem ipsum dolird</li>
    </ul>
  </div>
</footer>

</body>
</html>
```